Website Redesign Project Puzzle Vault Larkfield

We are an escape room company located in Ashburn, Virginia. We currently have a website https://www.puzzlevaultlarkfield.example based upon html/bootstrap/javascript/php/mysql and I'd like to keep it that way. I'm looking for someone upgrade the front page so it is more informative, cleaner, quicker to load, and optimizes the space for full sale opportunities.

Target Market(s)

Corporate Clients, Families, Friends. All ages

Industry/Entity Type

Entertainment Industry

Coding

Coded - Design and coding required

Number of Pages Required

3 page

Font styles to use
Other font styles liked:
• Similar to Facebook or Amazon

Requirements
Must have
• Must be mobile friendly. bootstrap. Lots of graphics (will provide) nice and easy to read fonts. Easy to read layout. Must look clean, fresh, exciting, and want to grab attention.
• Please visit my facebook page and website for more details. facebook.com/puzzlevaultlarkfield
Nice to have
• Same color as existing but open to options if they look nice.
Should not have
• Should not be wordpress or hard to modify.

```html
<!DOCTYPE html>
<html lang="en">
<head>
<meta charset="utf-8">
<title>Puzzle Vault Larkfield</title>
<link href="https://fonts.googleapis.com/css2?family=Montserrat:wght@400;500;600;700&display=swap" rel="stylesheet">
<style>
:root{
  --blue:#1692e0;
  --navy:#0f2036;
  --sky:#d4ecf8;
  --slate:#6597b2;
  --ink:#222;
  --wedge:#2a2b2e;
  --white:#fff;
  --muted:#5d6670;
}
*{box-sizing:border-box;margin:0;padding:0}
html,body{width:1200px;height:5333px;overflow:hidden}
body{position:relative;font-family:'Montserrat',sans-serif;color:var(--ink);background:var(--white)}
.abs{position:absolute}
.band{position:absolute;left:0;width:1200px}
.section-title{position:absolute;left:0;width:1200px;text-align:center;font-size:31px;font-weight:700;color:#1c1c1c}

/* header */
.brand{left:145px;top:24px;display:flex;align-items:center;gap:10px;color:var(--blue);font-weight:700;font-size:22px;line-height:1.1;width:190px}
.brand-square{width:30px;height:30px;background:var(--blue);flex:none}
.book-now{left:943px;top:25px;width:112px;height:31px;background:var(--blue);color:#fff;font-size:12px;font-weight:500;display:flex;align-items:center;justify-content:center}
.main-nav{right:145px;top:82px;display:flex;gap:34px;font-size:12.5px;color:#444;letter-spacing:.2px}
.main-nav .active{color:var(--blue)}

/* hero */
.hero{top:130px;height:584px;background:linear-gradient(135deg,#3d5f8a 0%,#7b6d69 35%,#c4a48f 55%,#3f5f95 80%,#1e2c4a 100%)}
.arrow{top:352px;width:30px;height:40px;background:var(--blue);display:flex;align-items:center;justify-content:center}

/* rooms */
.room{width:430px;height:124px}
.room-photo{position:absolute;left:0;top:0;width:120px;height:120px}
.room-info{position:absolute;left:130px;top:-2px;width:295px}
.room-name{color:var(--blue);font-size:19px;font-weight:500}
.room-diff{display:flex;align-items:center;gap:6px;font-size:11px;margin-top:4px}
.diff-bar{flex:1;height:5px;background:var(--blue);position:relative}
.diff-bar i{position:absolute;right:0;top:0;height:5px;background:#1d2430}
.room-text{font-size:10.5px;line-height:1.65;color:var(--muted);margin-top:8px}

/* corporate */
.corp-box{left:145px;top:1452px;width:910px;height:1037px;background:var(--navy)}
.corp-photo{left:145px;top:1452px;width:910px;height:389px;background:linear-gradient(180deg,#2a3a5c 0%,#6b5b55 45%,#c86a3a 70%,#7a4840 100%)}
.pkg{top:1841px;width:288px;height:232px;background:#fff}
.pkg h3{position:absolute;left:18px;top:16px;right:14px;font-size:19px;font-weight:500;line-height:1.2}
.pkg p{position:absolute;left:18px;top:74px;right:16px;font-size:10.3px;line-height:1.7;color:#444}
.pkg-foot{position:absolute;left:0;bottom:0;width:288px;height:39px;background:var(--blue);color:#fff;font-size:15px;padding:10px 18px}

.form-title{position:absolute;left:0;width:1200px;text-align:center;font-size:31px;font-weight:700}
.field{position:absolute;height:40px;border:1px solid #3c5c7e;font-size:11px;color:#8fb5d6;padding:13px 14px}
.field.light{border-color:#a9c8e0;background:#d4ecf8;color:#7a9ab5}
.select::after{content:"";position:absolute;right:16px;top:17px;border:5px solid transparent;border-top-color:currentColor}
.submit{position:absolute;width:98px;height:39px;background:var(--blue);color:#fff;font-weight:600;font-size:15px;display:flex;align-items:center;justify-content:center}

/* birthday */
.bday-photo{left:145px;top:2818px;width:455px;height:358px;background:linear-gradient(90deg,#d8b98e 0%,#b7a9c9 40%,#8f5e6a 70%,#c7c3d5 100%)}
.bday-panel{left:600px;top:2818px;width:455px;height:358px;background:var(--navy);color:#fff}
.bday-intro{position:absolute;left:31px;top:32px;width:395px;font-size:10px;line-height:1.8;color:#cfd9e4}
.bday-opt{position:absolute;left:31px;width:395px;font-size:15px;line-height:1.55;color:var(--blue)}
.note{position:absolute;left:31px;top:261px;width:393px;height:56px;border:1px solid #3c5c7e;display:flex;align-items:center;gap:10px;padding:0 18px;font-size:9.5px;color:#b8c7d6;line-height:1.5}
.note-icon{width:22px;height:22px;border-radius:50%;background:#9fb4c8;color:var(--navy);font-weight:700;font-size:13px;display:flex;align-items:center;justify-content:center;flex:none}
.bday-form{left:145px;top:3176px;width:910px;height:327px;background:var(--sky)}

/* how it works */
.hiw-lead{left:150px;top:3812px;width:900px;text-align:center;font-size:11px;line-height:1.75;color:#333}
.faq{position:absolute;left:145px;width:910px;height:37px;background:var(--slate);color:#fff;font-size:14px;padding:10px 22px;display:flex;justify-content:space-between;align-items:center}
.faq.open{background:var(--blue)}
.faq .tog{width:15px;height:15px;background:#fff;color:var(--slate);font-size:13px;font-weight:700;display:flex;align-items:center;justify-content:center;line-height:1}
.faq.open .tog{color:var(--blue)}
.faq-body{left:145px;top:3912px;width:910px;height:40px;background:#fff;font-size:10px;padding:14px 22px;color:#333}
.faq-body span{color:var(--blue)}

/* contact */
.contact-info{left:145px;top:4713px;width:455px;height:321px;background:var(--navy);color:var(--blue)}
.c-row{position:absolute;left:45px;display:flex;gap:20px;font-size:15.5px;line-height:1.55;width:380px}
.c-row svg{flex:none;margin-top:3px}
.map{left:600px;top:4713px;width:455px;height:321px;background:linear-gradient(135deg,#eceeea 0%,#e3e7e2 55%,#cfe6c6 80%,#b9dcb0 100%)}

/* footer */
.footer-links{left:145px;top:5246px;display:flex;gap:10px;font-size:10px;color:#9fb0c2}
.copy{left:145px;top:5280px;font-size:10px;color:#7f90a2}
.social{right:150px;top:5248px;display:flex;gap:20px}
.social span{width:14px;height:14px;border-radius:50%;background:#7f90a2}
</style>
</head>
<body>

<!-- Header -->
<header>
  <div class="abs brand"><span class="brand-square"></span><span>Puzzle Vault Larkfield</span></div>
  <a class="abs book-now">BOOK NOW</a>
  <nav class="abs main-nav">
    <span class="active">ESCAPE ROOMS</span><span>SPECIAL EVENTS</span><span>LOCATIONS</span><span>HOW IT WORKS</span><span>CONTACT US</span>
  </nav>
</header>

<!-- Hero -->
<section class="band hero" role="img" aria-label="Group photo of a large family celebrating after an escape room game"></section>
<div class="abs arrow" style="left:0"><svg width="12" height="18" viewBox="0 0 12 18"><path d="M9 2 3 9l6 7" stroke="#fff" stroke-width="2.5" fill="none"/></svg></div>
<div class="abs arrow" style="right:0"><svg width="12" height="18" viewBox="0 0 12 18"><path d="M3 2l6 7-6 7" stroke="#fff" stroke-width="2.5" fill="none"/></svg></div>
<svg class="band" style="top:600px" width="1200" height="120" viewBox="0 0 1200 120">
  <polygon points="0,115 1200,15 1200,120 0,120" fill="#fff"/>
  <polygon points="0,95 1200,-10 1200,15 0,115" fill="#1692e0"/>
  <polygon points="700,60 1200,10 1200,78" fill="#2a2b2e"/>
</svg>

<!-- Escape Rooms -->
<h2 class="section-title" style="top:788px">Escape Rooms</h2>
<div class="abs room" style="left:145px;top:848px">
  <div class="room-photo" role="img" aria-label="Elevator room with metal gate" style="background:linear-gradient(135deg,#5a4b3c,#b09a7c)"></div>
  <div class="room-info"><div class="room-name">Elevator</div>
    <div class="room-diff">Difficulty: 10/10 <span class="diff-bar"></span></div>
    <p class="room-text">The main elevators are down so you'll need to take the freight elevator to the top floor if you want to get your award. The last celebrity that attempted to do so wasn't so lucky.</p></div>
</div>
<div class="abs room" style="left:627px;top:848px">
  <div class="room-photo" role="img" aria-label="Players in the candy shop room" style="background:linear-gradient(135deg,#c8b8b0,#8a4a4a)"></div>
  <div class="room-info"><div class="room-name">Candy Shop</div>
    <div class="room-diff">Difficulty: 3/10 <span class="diff-bar"><i style="width:45px"></i></span></div>
    <p class="room-text">With all of the candy right before your eyes, find the golden ticket and win the prize!</p></div>
</div>
<div class="abs room" style="left:145px;top:1016px">
  <div class="room-photo" role="img" aria-label="Bank vault door" style="background:linear-gradient(135deg,#1c1f24,#4b4f55)"></div>
  <div class="room-info"><div class="room-name">Bank Heist</div>
    <div class="room-diff">Difficulty: 8/10 <span class="diff-bar"><i style="width:28px"></i></span></div>
    <p class="room-text">With your family held hostage, the mob gave you one choice - rob the bank in exchange for their freedom or its goodbyes forever.</p></div>
</div>
<div class="abs room" style="left:627px;top:1016px">
  <div class="room-photo" role="img" aria-label="Team in orange jumpsuits" style="background:linear-gradient(135deg,#3a3a48,#d8602c)"></div>
  <div class="room-info"><div class="room-name">Jail Break</div>
    <div class="room-diff">Difficulty: 8/10 <span class="diff-bar"><i style="width:28px"></i></span></div>
    <p class="room-text">One Guard. One Goal: get out.</p></div>
</div>

<!-- Corporate band -->
<div class="band" style="top:1270px;height:1350px;background:var(--sky)"></div>
<svg class="band" style="top:1215px" width="1200" height="115" viewBox="0 0 1200 115">
  <polygon points="0,0 1200,0 1200,20 0,108" fill="#fff"/>
  <polygon points="0,40 520,50 0,108" fill="#2a2b2e"/>
  <polygon points="300,65 1200,0 1200,20 0,108" fill="#1692e0" opacity="0"/>
  <polygon points="380,60 1200,8 1200,30 0,108" fill="#1692e0"/>
  <polygon points="0,40 400,58 0,100" fill="#2a2b2e"/>
</svg>

<h2 class="section-title" style="top:1392px">Corporate Events</h2>
<div class="abs corp-box"></div>
<div class="abs corp-photo" role="img" aria-label="Corporate team posing together, several in orange jumpsuits"></div>
<article class="abs pkg" style="left:159px"><h3>On-site multi-room</h3>
  <p>Come, enjoy, relax in our multi-room escape room facility with your team. With four different rooms to choose from we are able to accommodate up to 30 people in a single hour.</p>
  <div class="pkg-foot">Number of Players: 30+</div></article>
<article class="abs pkg" style="left:455px"><h3>Off-site Hot Seat Escape Room package</h3>
  <p>Enjoy a 2 or 4 hour escape room in the new thrilling Hot Seat challenge! Each player is given two minutes to solve the challenge at hand before they go up in smoke! Can you do it?</p>
  <div class="pkg-foot">Number of Players: 20 to 100</div></article>
<article class="abs pkg" style="left:751px"><h3>Off-site Custom Escape Room Package</h3>
  <p>Enjoy a customized escape room game to fit the theme you'd like to celebrate. You and your team will come in to work or what seems to be a normal work day until they arrive in an immersive experience for all to enjoy. Each game is customized and includes live actors.</p>
  <div class="pkg-foot">Number of Players: 30+</div></article>

<h2 class="form-title" style="top:2147px;color:#fff">Contact Us</h2>
<div class="field" style="left:159px;top:2203px;width:216px">Name</div>
<div class="field" style="left:380px;top:2203px;width:216px">Email</div>
<div class="field" style="left:601px;top:2203px;width:216px">Phone</div>
<div class="field select" style="left:822px;top:2203px;width:218px">Select a Package</div>
<div class="field" style="left:159px;top:2253px;width:881px;height:108px">Message</div>
<div class="submit" style="left:551px;top:2371px">Submit</div>

<svg class="band" style="top:2570px" width="1200" height="115" viewBox="0 0 1200 115">
  <polygon points="0,85 1200,35 1200,115 0,115" fill="#fff"/>
  <polygon points="0,70 1200,28 1200,40 0,110" fill="#1692e0"/>
  <polygon points="700,40 1200,0 1200,45" fill="#2a2b2e"/>
</svg>

<!-- Birthday -->
<h2 class="section-title" style="top:2756px">Birthday Parties</h2>
<div class="abs bday-photo" role="img" aria-label="Group holding tickets in the candy shop room"></div>
<div class="abs bday-panel">
  <p class="bday-intro">Celebrate this year in style by treating your family with an escape room birthday package. You and your loved ones have the choice of four escape rooms and will enjoy a private party afterwards in our party room. Either of these packages will be sure to satisfy your needs.</p>
  <p class="bday-opt" style="top:118px">a. A private escape room event with party room pizza and soda. Add just $150 to your escape room.</p>
  <p class="bday-opt" style="top:190px">b. A private escape room event with a party room rental. Bring your own food. Add just $125.</p>
  <div class="note"><span class="note-icon">i</span><span>Note: A $50 cleaning fee applies to all parties who don't clean after themselves</span></div>
</div>
<div class="abs bday-form"></div>
<h2 class="form-title" style="top:3233px">Contact Us</h2>
<div class="field light" style="left:159px;top:3292px;width:216px">Name</div>
<div class="field light" style="left:380px;top:3292px;width:216px">Email</div>
<div class="field light" style="left:601px;top:3292px;width:216px">Phone</div>
<div class="field light select" style="left:822px;top:3292px;width:218px">Select a Package</div>
<div class="field light select" style="left:159px;top:3337px;width:216px">Group Size</div>
<div class="field light" style="left:380px;top:3337px;width:660px">Message</div>
<div class="submit" style="left:551px;top:3401px">Submit</div>

<!-- How it works -->
<div class="band" style="top:3690px;height:880px;background:var(--sky)"></div>
<svg class="band" style="top:3610px" width="1200" height="120" viewBox="0 0 1200 120">
  <polygon points="0,120 1200,60 1200,120" fill="#d4ecf8"/>
  <polygon points="0,20 500,45 0,82" fill="#2a2b2e"/>
  <polygon points="0,82 1200,25 1200,60 0,120" fill="#1692e0"/>
  <polygon points="0,95 1200,60 1200,120 0,120" fill="#d4ecf8"/>
</svg>
<h2 class="section-title" style="top:3757px">How It Works</h2>
<p class="abs hiw-lead">An escape room is a themed environment where you and your friends must work together to complete the objectives through solving puzzles before time runs out. Most missions will lock you in while some of our missions do not.</p>
<div class="faq open" style="top:3875px"><span>How do I make a reservation?</span><span class="tog">−</span></div>
<div class="abs faq-body">Click on the Book now button or <span>click here</span></div>
<div class="faq" style="top:3972px"><span>How long does an escape last?</span><span class="tog">+</span></div>
<div class="faq" style="top:4020px"><span>Is there an age limit?</span><span class="tog">+</span></div>
<div class="faq" style="top:4068px"><span>I'm pregnant, can I participate?</span><span class="tog">+</span></div>
<div class="faq" style="top:4116px"><span>How can I redeem a voucher or promo code?</span><span class="tog">+</span></div>
<div class="faq" style="top:4164px"><span>Where do I park?</span><span class="tog">+</span></div>
<div class="faq" style="top:4212px"><span>Do I have to sign a liability waiver?</span><span class="tog">+</span></div>
<div class="faq" style="top:4260px"><span>Which room is the most challenging?</span><span class="tog">+</span></div>
<div class="faq" style="top:4308px"><span>What is the cancellation policy?</span><span class="tog">+</span></div>
<div class="faq" style="top:4356px"><span>What time should we arrive?</span><span class="tog">+</span></div>
<svg class="band" style="top:4505px" width="1200" height="90" viewBox="0 0 1200 90">
  <polygon points="0,50 1200,0 1200,90 0,90" fill="#fff"/>
  <polygon points="0,50 1200,0 1200,20 0,75" fill="#1692e0"/>
  <polygon points="0,75 1200,20 1200,90 0,90" fill="#fff"/>
</svg>

<!-- Contact -->
<h2 class="section-title" style="top:4659px">Contact Us</h2>
<div class="abs contact-info">
  <div class="c-row" style="top:68px"><svg width="14" height="18" viewBox="0 0 14 18"><path d="M7 0a7 7 0 0 0-7 7c0 5 7 11 7 11s7-6 7-11a7 7 0 0 0-7-7zm0 10a3 3 0 1 1 0-6 3 3 0 0 1 0 6z" fill="#1692e0"/></svg><span>1180 Harlow Mill Road, Suite 14, Larkfield, VA 20999</span></div>
  <div class="c-row" style="top:135px"><svg width="16" height="16" viewBox="0 0 16 16"><path d="M3 1l3 0 1 4-2 1c1 2 3 4 5 5l1-2 4 1v3c0 1-1 2-2 2C7 15 1 9 1 3c0-1 1-2 2-2z" fill="#1692e0"/></svg><span>Phone: (555) 014 2277</span></div>
  <div class="c-row" style="top:176px"><svg width="16" height="13" viewBox="0 0 16 13"><rect width="16" height="13" rx="1" fill="#1692e0"/><path d="M1 1l7 6 7-6" stroke="#0f2036" stroke-width="1.5" fill="none"/></svg><span>E-mail: hello@puzzlevaultlarkfield.example</span></div>
  <div class="c-row" style="top:223px"><svg width="16" height="16" viewBox="0 0 16 16"><circle cx="8" cy="8" r="8" fill="#1692e0"/><path d="M8 3v5l3 2" stroke="#0f2036" stroke-width="1.6" fill="none"/></svg><span>Hours: Wednesday - Fridays (4 to 10pm)<br>Weekends (11am to 9pm).</span></div>
</div>
<div class="abs map" role="img" aria-label="Street map showing the venue location"></div>

<!-- Footer -->
<svg class="band" style="top:5140px" width="1200" height="193" viewBox="0 0 1200 193">
  <polygon points="0,45 1200,0 1200,193 0,193" fill="#0f2036"/>
  <polygon points="0,30 1200,-15 1200,18 0,60" fill="#1692e0"/>
  <polygon points="0,0 0,60 500,40" fill="#2a2b2e"/>
  <polygon points="0,60 1200,18 1200,193 0,193" fill="#0c1a2c"/>
</svg>
<footer>
  <nav class="abs footer-links"><span>Escape Rooms</span>|<span>Special Events</span>|<span>Locations</span>|<span>How It Works</span>|<span>Contact Us</span>|<span>Book Now</span></nav>
  <p class="abs copy">Copyright © 2019 Puzzle Vault Larkfield. All rights reserved.</p>
  <div class="abs social"><span></span><span></span><span></span></div>
</footer>

</body>
</html>
```